Business Card Design For Office Furniture Clearance Company

Kestrel Office Clearance - our company name pretty much explains what we do, we clear offices for high end clients, mainly plc's and large international companies.

We require a nice looking business card that displays professionalism but without being too serious.

It would be nice to see just a little more than a conventional boring business card, make sure you add some flare.

Industry/Entity Type

Office Furniture

Contact Information for Business Card

CARD 1

Mark Holloway
Director
mark@kestrelofficeclearance.co.uk
m: 07700 153928

t: 01632 960418
www.kestrelofficeclearance.co.uk

Kestrel Office Clearance
Unit K4 B
2-8 Fenwick Lane
Ashwell Green
Harbourne Vale
ZZ9 4QT

Office clearances at no cost… tidy, quick and done right.

CARD 2

Peter Radford
Director
peter@kestrelofficeclearance.co.uk
m: 07700 382615

t: 01632 960418

Kestrel Office Clearance
Unit K4 B
2-8 Fenwick Lane
Ashwell Green
Harbourne Vale
ZZ9 4QT

Font styles to use
Sans Serif

Requirements
Must have
• A white background - as we have a blue logo.
Nice to have
• Nice use of the logo - play around with this and dissect it.

```html
<!DOCTYPE html>
<html lang="en">
<head>
<meta charset="utf-8">
<title>Kestrel Office Clearance – Business Cards</title>
<link rel="stylesheet" href="https://fonts.googleapis.com/css2?family=Open+Sans:wght@400;600&display=swap">
<style>
  :root {
    --backdrop: #3b322d;
    --card-white: #f4f4f4;
    --card-black: #1c1c1c;
    --brand-blue: #0a78c2;
    --ink: #2a2a2a;
    --band-text: #ffffff;
  }
  * { box-sizing: border-box; margin: 0; padding: 0; }
  html, body {
    width: 1200px; height: 844px; overflow: hidden;
    background: var(--backdrop);
    font-family: "Open Sans", Arial, sans-serif;
  }
  .card-pair {
    position: absolute; top: 247px; left: 40px;
    display: flex; gap: 40px;
  }
  .card {
    position: relative; width: 540px; height: 350px;
    box-shadow: 0 10px 28px rgba(0,0,0,.45);
    overflow: hidden;
  }
  .card-front { background: var(--card-white); color: var(--ink); }
  .card-back { background: var(--card-black); }

  .brand-mark {
    position: absolute; top: 30px; right: 34px;
    display: flex; flex-direction: column; align-items: center; gap: 8px;
  }
  .brand-mark .brand-dot {
    width: 150px; height: 150px; border-radius: 50%;
    background: var(--brand-blue);
  }
  .brand-mark .brand-name {
    color: var(--brand-blue); font-weight: 600; font-size: 18px;
  }

  .contact-block { position: absolute; left: 36px; bottom: 28px; line-height: 1.3; }
  .person-name { color: var(--brand-blue); font-weight: 600; font-size: 21px; }
  .person-role { font-size: 13px; margin-bottom: 6px; }
  .company-name { color: var(--brand-blue); font-weight: 600; font-size: 18px; }
  .address { font-style: normal; font-size: 14.5px; margin-bottom: 12px; }
  .contact-list { list-style: none; font-size: 14.5px; }
  .contact-list li { display: flex; align-items: center; gap: 8px; }
  .contact-list svg { width: 12px; height: 12px; fill: var(--brand-blue); flex: none; }

  .back-mark {
    position: absolute; top: 36px; left: 50%; transform: translateX(-50%);
    display: flex; flex-direction: column; align-items: center; gap: 8px;
  }
  .back-mark .brand-dot {
    width: 120px; height: 120px; border-radius: 50%; background: var(--brand-blue);
  }
  .back-mark .brand-name { color: var(--brand-blue); font-weight: 600; font-size: 18px; }
  .tagline-band {
    position: absolute; left: 0; right: 0; top: 220px; height: 38px;
    background: var(--brand-blue); color: var(--band-text);
    display: flex; align-items: center; justify-content: center;
    font-size: 14px; font-weight: 600; letter-spacing: .3px; text-transform: uppercase;
    white-space: nowrap;
  }
</style>
</head>
<body>
  <main class="card-pair">
    <section class="card card-front" aria-label="Business card front">
      <div class="brand-mark">
        <span class="brand-dot"></span>
        <span class="brand-name">Kestrel</span>
      </div>
      <div class="contact-block">
        <p class="person-name">Mark Holloway</p>
        <p class="person-role">Director</p>
        <p class="company-name">Kestrel Office Clearance</p>
        <address class="address">
          Unit K4 B, 2-8 Fenwick Lane<br>
          Ashwell Green, Harbourne Vale<br>
          ZZ9 4QT
        </address>
        <ul class="contact-list">
          <li><svg viewBox="0 0 12 12"><rect x="2.5" y="0" width="7" height="12" rx="1.5"/></svg>07700 153928</li>
          <li><svg viewBox="0 0 12 12"><path d="M2 0l3 3-1.5 1.5c.8 1.7 2.3 3.2 4 4L9 7l3 3-2 2C5 12 0 7 0 2z"/></svg>01632 960418</li>
          <li><svg viewBox="0 0 12 12"><path d="M0 2h12v1L6 7 0 3zM0 4.5l6 4 6-4V10H0z"/></svg>mark@kestrelofficeclearance.co.uk</li>
          <li><svg viewBox="0 0 12 12"><circle cx="6" cy="6" r="6"/></svg>www.kestrelofficeclearance.co.uk</li>
        </ul>
      </div>
    </section>

    <section class="card card-back" aria-label="Business card back">
      <div class="back-mark">
        <span class="brand-dot"></span>
        <span class="brand-name">Kestrel</span>
      </div>
      <p class="tagline-band">Office clearances at no cost… tidy, quick and done right</p>
    </section>
  </main>
</body>
</html>
```